Bandbanner für Melodic Metal Band
Zielgruppe
Velvet Harbor ist eine Melodic Metal Band.
Wir brauchen ein neues Design für Backdrops (Bandbanner) die wir in verschiedenen Grössen drucken könnten.
(Bisher hatten wir die Grössen 500 cm x 300 cm, 400 cm x 250 cm und 200 cm x 200 cm)
Unser Bandlogo soll modern und inspiriert rüberkommen, um unsere Musik und Show zusätzlich zu unterstreichen.
Aufgabenstellung
- das Bandlogo soll stylisch und cool präsentiert sein (z.B. mit zusätzlichen Elementen ergänzt, umspielt, umrahmt... )
- einzigartig, Blickfang, auf uns zugeschnitten
- Das Design soll neu und neutral sein. Also nicht direkt bezogen auf eines unserer Alben. Wir möchten es für verschiedene Zwecke und für längere Zeit benutzen können
- modern, cool, vielleicht frech, kann Farben enthalten, hell/dunkel, mystisch
- soll zu unserem ganzen Auftreten und Style passen
- unsere Musik und Inhalte sind melodiös, modern, mal hart, mal sanfter, mal etwas dunkler, anklagend oder nachdenklich aber immer mit einer Prise Helligkeit und Hoffnung, nicht destruktiv. Deshalb nicht zu morbide oder zu klischeehaft, aber es darf gerne mysteriös oder melancholisch oder auch schlicht und speziell sein
(Das Logo und Sign könnten wir übrigens als AI, CDR, EPS, JPG, PDF, PNG und PSD zur Verfügung stellen).

```html
<!DOCTYPE html>
<html lang="de">
<head>
<meta charset="utf-8">
<title>Velvet Harbor – Bandbanner</title>
<link href="https://fonts.googleapis.com/css2?family=Cormorant+Garamond:wght@600;700&display=swap" rel="stylesheet">
<style>
  :root {
    --night: #121412;
    --forest: #1c221f;
    --treeline: #161a18;
    --mist: #303834;
    --ember: rgba(90,55,32,0.40);
    --flare: rgba(255,225,180,0.55);
    --silver: #dededa;
    --white: #f4f4f2;
  }
  * { margin: 0; padding: 0; box-sizing: border-box; }
  html, body {
    width: 1200px; height: 675px; overflow: hidden;
    background: var(--night);
  }
  .banner {
    position: relative;
    width: 1200px; height: 675px;
    overflow: hidden;
    font-family: "Cormorant Garamond", Georgia, serif;
    font-weight: 600;
  }
  .banner__scene {
    position: absolute; inset: 0;
    background:
      radial-gradient(circle at 706px 294px, var(--flare) 0, rgba(255,200,140,0.15) 14px, transparent 60px),
      radial-gradient(ellipse 22% 10% at 50% 82%, var(--ember), transparent 70%),
      radial-gradient(ellipse 55% 28% at 55% 32%, rgba(75,90,82,0.35), transparent 70%),
      linear-gradient(180deg, var(--mist) 0%, var(--forest) 22%, var(--treeline) 48%, #141614 70%, var(--night) 100%);
  }
  .banner__bandname {
    position: absolute;
    left: 0; right: 0; top: 262px;
    text-align: center;
    white-space: nowrap;
    color: var(--silver);
    font-size: 112px;
    font-weight: 700;
    line-height: 1;
    letter-spacing: 5px;
    text-transform: uppercase;
  }
  .banner__emblem {
    position: absolute;
    left: 545px; top: 494px;
    width: 108px; height: 108px;
    display: flex; align-items: center; justify-content: center;
  }
  .banner__emblem-ring {
    position: absolute; inset: 0;
    border: 2px solid var(--silver);
    border-radius: 50%;
  }
  .banner__emblem-name {
    color: var(--silver);
    font-size: 17px;
    text-align: center;
    line-height: 1.1;
  }
  .banner__social {
    position: absolute;
    left: 859px; top: 606px;
    display: flex; align-items: center; gap: 14px;
    color: var(--white);
    font-size: 17px;
    letter-spacing: -0.3px;
  }
  .banner__social-links { display: flex; gap: 14px; margin-left: 4px; }
  .banner__social-dot {
    width: 18px; height: 18px;
    border-radius: 50%;
    background: var(--white);
  }
</style>
</head>
<body>
  <main class="banner">
    <div class="banner__scene" role="img" aria-label="Nächtlicher, nebliger Nadelwald unter dunklem Himmel mit einem hellen Lichtschein hinter den Baumwipfeln"></div>
    <h1 class="banner__bandname">Velvet Harbor</h1>
    <div class="banner__emblem">
      <span class="banner__emblem-ring"></span>
      <span class="banner__emblem-name">Velvet<br>Harbor</span>
    </div>
    <div class="banner__social">
      <span>VelvetHarbor/</span>
      <span class="banner__social-links" aria-label="Soziale Netzwerke">
        <span class="banner__social-dot"></span>
        <span class="banner__social-dot"></span>
        <span class="banner__social-dot"></span>
        <span class="banner__social-dot"></span>
      </span>
    </div>
  </main>
</body>
</html>
```